Larkspur Talent IT Recruiting firm needs a business card design for Recruiters, Sourcers, and Account

We need business cards that allow us to change all contact info, names, titles (Recruiter, Sourcer, Account Manager, Director, CEO, etc) per person since we have three offices, in three cities, Phoenix, Austin, and Las Vegas. We do recruiting and contractors for IT positions (Developers, Architects, Software Engineers, Security Engineers, Help Desk, DBAs, PMs, Scrum Masters, etc.) Our client companies are very diverse from Meridian 100 to silicone Valley type start-ups.

So, while we what hip, techie, and quirky, it still needs to be professional. Primary color we use is blue, with silver as a secondary color.

Target Market(s)

IT, Technology

Industry/Entity Type

Business

Contact Information for Business Card

Company name: Larkspur Talent, Inc.
Website: www.larkspurtalent.example
Logos for Careerloop, Blipster, and Myriada

Name, Title, Office Number, Cell Number, email

Font styles to use
Serif
Sans Serif

Colors
0455a3
d5d5d5

Requirements
Nice to have
• The grey I selected below is not necessary - but, would like silver included. I included a card design (File 3: LTI early trial example.jpg) that I had started on. It's very rough, and not quite what we're looking for, but what we did like is the logo, big, maybe a bit faded, off center, goes out of frame, etc. Still looking for other ideas - you are the pros! But, just an idea of a design element we liked.

```html
<!DOCTYPE html>
<html lang="en">
<head>
<meta charset="utf-8">
<title>Larkspur Talent — Business Card</title>
<link href="https://fonts.googleapis.com/css2?family=Marcellus&family=PT+Sans:wght@400&display=swap" rel="stylesheet">
<style>
  :root {
    --backdrop: #1a1a1a;
    --card-white: #ffffff;
    --brand-blue: #0455a3;
    --brand-blue-light: #0a8fd6;
    --ink-dark: #2b2b2b;
    --band-grey: #555555;
    --back-grey: #575757;
    --silver: #d5d5d5;
    --white: #ffffff;
  }
  * { margin: 0; padding: 0; box-sizing: border-box; }
  html, body { width: 1200px; height: 907px; overflow: hidden; background: var(--backdrop); }
  .stage { position: relative; width: 1200px; height: 907px; }
  .card {
    position: absolute; left: 300px; width: 600px; height: 342px; overflow: hidden;
    box-shadow: 0 6px 18px rgba(0,0,0,.6);
  }
  .card--front { top: 98px; background: var(--card-white); }
  .card--back { top: 475px; background: var(--back-grey); }

  .front-waves { position: absolute; inset: 0; }

  .brand { position: absolute; display: flex; align-items: center; gap: 10px; }
  .brand__dot { border-radius: 50%; flex: none; }
  .brand__name { display: flex; flex-direction: column; align-items: flex-end;
    font-family: "Marcellus", serif; text-transform: uppercase; line-height: 1; }
  .brand__line { letter-spacing: 3px; }
  .tagline { position: absolute; font-family: "Marcellus", serif; text-transform: uppercase; letter-spacing: 2px; white-space: nowrap; }

  .card--front .brand { left: 50px; top: 56px; }
  .card--front .brand__dot { width: 40px; height: 40px; background: var(--brand-blue-light); }
  .card--front .brand__name { color: var(--ink-dark); }
  .card--front .brand__line--main { font-size: 40px; }
  .card--front .brand__line--sub { font-size: 27px; margin-top: 4px; }
  .card--front .tagline { left: 62px; top: 141px; font-size: 14.5px; color: var(--ink-dark); }

  .person { position: absolute; left: 31px; top: 261px; color: var(--white); font-family: "PT Sans", sans-serif; }
  .person__name { font-size: 21px; }
  .person__title { font-size: 15px; margin-top: 3px; }

  .contacts { position: absolute; right: 46px; top: 224px; list-style: none; font-family: "PT Sans", sans-serif; color: var(--white); font-size: 15px; }
  .contacts li { display: flex; justify-content: flex-end; align-items: center; gap: 9px; height: 22.5px; }
  .contacts svg { width: 14px; height: 14px; flex: none; }

  .emblem-area {
    position: absolute; left: 8px; top: 6px; width: 334px; height: 334px; border-radius: 50%;
    background: radial-gradient(circle at 50% 40%, #7a7a7a 0%, #686868 55%, #5d5d5d 100%);
  }
  .socials { position: absolute; right: 36px; top: 34px; display: flex; gap: 12px; list-style: none;
    font-family: "PT Sans", sans-serif; font-size: 12px; color: var(--white); }
  .socials li { display: flex; align-items: center; gap: 5px; }
  .socials li::before { content: ""; width: 10px; height: 10px; background: var(--brand-blue-light); border-radius: 2px; }

  .card--back .brand { right: 34px; top: 234px; }
  .card--back .brand__dot { width: 34px; height: 34px; background: var(--white); }
  .card--back .brand__name { color: var(--white); }
  .card--back .brand__line--main { font-size: 33px; }
  .card--back .brand__line--sub { font-size: 22px; margin-top: 3px; }
  .card--back .tagline { right: 34px; top: 298px; font-size: 12.5px; color: var(--white); }
</style>
</head>
<body>
<main class="stage">
  <section class="card card--front" aria-label="Business card front">
    <svg class="front-waves" viewBox="0 0 600 342" preserveAspectRatio="none" aria-hidden="true">
      <defs>
        <radialGradient id="blueGlow" cx="62%" cy="70%" r="70%">
          <stop offset="0" stop-color="#0a8fd6"/>
          <stop offset="1" stop-color="#0c4fa8"/>
        </radialGradient>
      </defs>
      <path d="M60 212 Q360 200 600 128 L600 148 Q400 218 60 212 Z" fill="var(--band-grey)"/>
      <path d="M0 204 Q310 250 600 153 L600 342 L0 342 Z" fill="#ffffff"/>
      <path d="M0 207 Q310 253 600 157 L600 342 L0 342 Z" fill="url(#blueGlow)"/>
    </svg>

    <div class="brand">
      <span class="brand__dot"></span>
      <span class="brand__name"><span class="brand__line brand__line--main">Larkspur</span><span class="brand__line brand__line--sub">Talent</span></span>
    </div>
    <p class="tagline">Connecting Tech Talent</p>

    <div class="person">
      <p class="person__name">Dana Whitlow</p>
      <p class="person__title">Manager</p>
    </div>

    <ul class="contacts">
      <li>555-014-2271
        <svg viewBox="0 0 14 14" aria-hidden="true"><path d="M3 1 L6 4 L4.5 6 Q6 9 8.5 10 L10 8.5 L13 11.5 L11 13 Q4 12 1 3 Z" fill="#fff"/></svg></li>
      <li>555-019-8364
        <svg viewBox="0 0 14 14" aria-hidden="true"><rect x="3.5" y="1" width="7" height="12" rx="1.2" fill="none" stroke="#fff" stroke-width="1.4"/><rect x="5" y="3" width="4" height="4" fill="#fff"/></svg></li>
      <li>info@larkspurtalent.example
        <svg viewBox="0 0 14 14" aria-hidden="true"><rect x="1" y="3" width="12" height="8" fill="#fff"/><path d="M1 3 L7 8 L13 3" fill="none" stroke="#0c4fa8" stroke-width="1"/></svg></li>
      <li>www.larkspurtalent.example
        <svg viewBox="0 0 14 14" aria-hidden="true"><circle cx="7" cy="7" r="5.5" fill="none" stroke="#fff" stroke-width="1.2"/><ellipse cx="7" cy="7" rx="2.3" ry="5.5" fill="none" stroke="#fff"/><path d="M1.5 7 H12.5" stroke="#fff"/></svg></li>
    </ul>
  </section>

  <section class="card card--back" aria-label="Business card back">
    <div class="emblem-area" role="img" aria-label="Large faded brand emblem decoration"></div>
    <ul class="socials">
      <li>Careerloop</li>
      <li>Blipster</li>
      <li>Myriada</li>
    </ul>
    <div class="brand">
      <span class="brand__dot"></span>
      <span class="brand__name"><span class="brand__line brand__line--main">Larkspur</span><span class="brand__line brand__line--sub">Talent</span></span>
    </div>
    <p class="tagline">Connecting Tech Talent</p>
  </section>
</main>
</body>
</html>
```